Pediatric Practice Flyer Design

I need marketing flyer created for distribution. It is for a pediatric clinic. Need some realistic eye catching design and content. I already have a logo that will go on top of the flyer. I will be using lumoraxen for flyer print service. So need it copyable for printing. Again, need eye catching content as well. We are planning on opening the clinic in December.

```html
<!DOCTYPE html>
<html lang="en">
<head>
<meta charset="utf-8">
<title>Meadowbrook Kids Care Pediatrics – Opening Soon Flyer</title>
<link rel="stylesheet" href="https://fonts.googleapis.com/css2?family=Roboto:wght@400;500;700&family=Oswald:wght@500;600&family=Merienda:wght@700&family=Courgette&family=Kalam:wght@700&display=swap">
<style>
  :root {
    --stage: #3a3a3a;
    --paper: #ffffff;
    --magenta: #e6158c;
    --orange: #f7a02a;
    --teal: #1fa89a;
    --blue: #1c7ac4;
    --purple: #6b3a9c;
    --red: #e5262d;
    --ink: #222222;
    --photo-warm: #e9ddd3;
    --photo-cool: #d9e4ec;
  }
  * { margin: 0; padding: 0; box-sizing: border-box; }
  html, body {
    width: 1200px; height: 1177px; overflow: hidden;
    background: var(--stage);
  }
  .flyer {
    position: absolute; left: 238px; top: 116px;
    width: 730px; height: 944px;
    background: var(--paper); overflow: hidden;
    font-family: "Roboto", sans-serif; color: var(--ink);
  }
  .flyer-shapes { position: absolute; inset: 0; }
  .brand { position: absolute; left: 36px; top: 34px; display: flex; align-items: center; gap: 22px; }
  .brand-dot { width: 120px; height: 120px; border-radius: 50%; background: var(--orange); }
  .brand-name {
    font-family: "Roboto", sans-serif; font-weight: 700; color: var(--magenta);
    font-size: 44px; line-height: 1.05;
  }
  .brand-name small { display: block; font-size: 24px; letter-spacing: 1px; text-align: right; }
  .doctor { position: absolute; left: 262px; top: 158px; width: 450px; }
  .doctor-name {
    font-family: "Kalam", cursive; font-weight: 700; color: var(--magenta);
    font-size: 22px; line-height: 30px; margin-left: 12px;
  }
  .doctor-bio {
    font-size: 15px; line-height: 19.5px; text-align: center;
    white-space: nowrap;
  }
  .opening {
    position: absolute; left: 378px; top: 324px; width: 280px; text-align: center; color: #fff;
  }
  .opening-title { font-family: "Oswald", sans-serif; font-weight: 600; font-size: 58px; line-height: 1.0; }
  .opening-rule { border-top: 3px dotted #fff; margin: 16px 14px 10px; }
  .opening-date { font-family: "Merienda", cursive; font-weight: 700; font-size: 28px; line-height: 1.35; }
  .offer { position: absolute; left: 40px; top: 688px; }
  .offer-line { display: flex; align-items: baseline; gap: 12px; border-bottom: 4px solid var(--magenta); padding-bottom: 2px; }
  .offer-free { font-family: "Oswald", sans-serif; font-weight: 600; font-size: 58px; color: var(--red); line-height: 1; }
  .offer-what { font-family: "Roboto", sans-serif; font-weight: 700; font-size: 39px; color: var(--purple); }
  .offer-note { font-family: "Courgette", cursive; font-size: 27px; color: var(--teal); margin-top: 4px; }
  .contact { position: absolute; left: 0; top: 813px; color: #fff; font-size: 14px; font-style: normal; }
  .contact p { height: 22px; line-height: 22px; white-space: nowrap; display: flex; align-items: center; }
  .contact .address { padding-left: 118px; }
  .contact .phones { padding-left: 98px; }
  .contact .fax { display: inline-flex; align-items: center; gap: 7px; margin-left: 24px; }
  .contact .fax svg { display: block; }
  .contact .email { padding-left: 84px; }
  .contact .web { padding-left: 66px; font-size: 20px; font-weight: 700; margin-top: 6px; }
</style>
</head>
<body>
  <main class="flyer">
    <svg class="flyer-shapes" viewBox="0 0 730 944" width="730" height="944">
      <rect class="photo photo-checkup" x="0" y="300" width="560" height="362" fill="var(--photo-warm)" role="img" aria-label="Photo: smiling pediatrician listening as a young girl with a teddy bear uses a stethoscope"/>
      <polygon class="photo photo-boy" points="546,560 730,560 730,903 386,903" fill="var(--photo-cool)" role="img" aria-label="Photo: curly-haired toddler getting a stethoscope check-up"/>
      <polygon class="accent-teal" points="635,0 730,0 730,166" fill="var(--teal)"/>
      <polygon class="accent-orange-small" points="158,169 208,169 183,221" fill="var(--orange)"/>
      <polygon class="accent-magenta" points="232,172 158,300 308,300" fill="var(--magenta)"/>
      <polygon class="opening-banner" points="308,300 730,300 518,662" fill="var(--orange)"/>
      <polygon class="contact-band" points="86,805 425,805 376,915 40,915" fill="var(--blue)"/>
      <polygon class="contact-strip" points="48,805 86,805 40,915 0,915 0,880" fill="var(--purple)"/>
      <g class="contact-icons" fill="#fff">
        <circle cx="72" cy="818" r="5.5"/>
        <polygon points="67,820 77,820 72,829"/>
        <circle cx="72" cy="818" r="2.2" fill="var(--purple)"/>
        <path d="M55,837 q2,-2 4,0 l2,3 q1,2 -1,3 q2,4 6,6 q1,-2 3,-1 l3,2 q2,2 0,4 q-3,3 -8,0 q-7,-5 -10,-11 q-2,-4 1,-6 Z"/>
        <rect x="41" y="861" width="14" height="10" rx="1"/>
        <path d="M41,861 L48,867 L55,861" stroke="var(--purple)" stroke-width="1.5" fill="none"/>
        <circle cx="34" cy="894" r="7"/>
        <path d="M27,894 h14 M34,887 q-4,7 0,14 M34,887 q4,7 0,14" stroke="var(--purple)" stroke-width="1.2" fill="none"/>
      </g>
      <rect class="footer-bar" x="0" y="918" width="730" height="26" fill="var(--magenta)"/>
    </svg>

    <header class="brand">
      <span class="brand-dot"></span>
      <h1 class="brand-name">Meadowbrook Kids<small>CARE PEDIATRICS</small></h1>
    </header>

    <section class="doctor">
      <h2 class="doctor-name">Dr. Lena Marwick</h2>
      <p class="doctor-bio">Dr. Marwick is an experienced and qualified pediatrician<br>who has served in various communities in Virginia and<br>North Carolina. She had also been recognized as<br>Capital Health Review's Top Doctor, 2019 and best Female<br>Doctor of Annandale.</p>
    </section>

    <section class="opening">
      <h2 class="opening-title">OPENING<br>SOON</h2>
      <div class="opening-rule"></div>
      <p class="opening-date">December<br>2022</p>
    </section>

    <section class="offer">
      <div class="offer-line"><span class="offer-free">FREE</span><span class="offer-what">1st Consultation</span></div>
      <p class="offer-note">Accepting New Patients</p>
    </section>

    <address class="contact">
      <p class="address">482 Brookfield Ave, Suite 12, Cary NC 27519.</p>
      <p class="phones"><span class="phone">919-555-0142</span><span class="fax"><svg width="13" height="12" viewBox="0 0 13 12" aria-hidden="true"><rect x="3" y="0" width="7" height="4" fill="#fff"/><rect x="0" y="4" width="13" height="8" rx="1" fill="#fff"/></svg>919-555-0187</span></p>
      <p class="email">office@mbkpediatrics.com</p>
      <p class="web">www.mbkpediatrics.com</p>
    </address>
  </main>
</body>
</html>
```